Create a business promotion flyer to leave in customer mailboxes. We are a bulk petroleum supplier, servicing any industry that requires diesel. Base in griffith NSW, servicing griffith area and surrounds.

Business Name - Terra Diesel
Fuel@terradiesel-example.com.au
Owen - 0491 570 362 ohartley@terradiesel-example.com.au
Liam - 0491 570 718 lprosser@terradiesel-example.com.au
Simon - 0491 570 905 skenway@terradiesel-example.com.au
Office 02 5550 1734

Bulk Fuel deliveries.
Oils & lubricants
Local Family owned business

```html
<!DOCTYPE html>
<html lang="en">
<head>
<meta charset="utf-8">
<title>Terra Diesel – Bulk Fuel Flyer</title>
<link rel="stylesheet" href="https://fonts.googleapis.com/css2?family=Poppins:wght@400;500;600;700;800&family=Oswald:wght@500;600;700&display=swap">
<style>
  :root{
    --red:#e8302a;
    --grey:#666666;
    --ink:#222222;
    --bar:#232323;
    --white:#ffffff;
    --pale:#eeeded;
  }
  *{box-sizing:border-box;margin:0;padding:0}
  html,body{width:980px;height:1200px;overflow:hidden;background:#d9d9d9}
  .flyer{position:relative;width:980px;height:1200px;background:var(--white);overflow:hidden;font-family:"Poppins",sans-serif}

  .hero-photo{position:absolute;left:0;top:0;width:980px;height:530px;
    background:linear-gradient(180deg,#9fc6e8 0%,#cfe2f2 38%,#b9bfc6 62%,#8f9297 80%,#a8a6a2 100%)}
  .hero-shapes{position:absolute;left:0;top:0}

  .brand-name{position:absolute;left:40px;top:118px;font-weight:600;font-size:40px;color:var(--red);letter-spacing:-0.5px}

  .headline{position:absolute;right:36px;top:28px;font-weight:700;font-size:66px;letter-spacing:-1.5px;line-height:1.2}
  .headline .first{color:var(--red)}
  .headline .second{color:var(--grey)}

  .promise{position:absolute;right:36px;top:138px;width:515px;height:32px;border-top:1.5px solid var(--grey);border-bottom:1.5px solid var(--grey);
    display:flex;justify-content:space-between;align-items:center;font-weight:800;font-size:16.5px;color:#3a3a3a}
  .promise span{display:flex;align-items:center;gap:4px}
  .tick{width:15px;height:15px}

  .services-panel{position:absolute;left:0;top:520px;width:430px;height:680px;background:var(--grey);border-top-right-radius:18px}
  .service{position:absolute;left:45px;display:flex;align-items:center}
  .service-icon{width:112px;height:112px;flex:none;border-radius:50%;background:var(--pale);border:2px solid var(--white);box-shadow:0 0 0 1px #8a8a8a;display:flex;align-items:center;justify-content:center}
  .service-text{margin-left:34px;color:#f3f3f3;font-size:26px;font-weight:500;line-height:1.12}
  .divider{position:absolute;left:248px;width:156px;border-top:1.5px dashed #e6e6e6}

  .base-badge{position:absolute;left:548px;top:452px;width:284px;height:284px;border-radius:50%;border:10px solid var(--grey);overflow:hidden;
    background:radial-gradient(circle at 50% 45%,#f4f4f4 0%,#e4e4e4 100%)}
  .base-text{position:absolute;left:0;right:0;top:52px;text-align:center;font-family:"Oswald",sans-serif;line-height:1}
  .base-text .small{color:var(--red);font-size:27px;font-weight:600}
  .base-text .town{color:var(--red);font-size:48px;font-weight:700;letter-spacing:1px;margin-top:2px}
  .base-text .state{color:var(--ink);font-size:36px;font-weight:600;opacity:.85;margin-top:2px}
  .pin{position:absolute;left:118px;top:190px}

  .service-band{position:absolute;left:457px;top:713px;width:523px;height:110px;background:var(--red);border-radius:55px 0 0 55px}
  .band-icon{position:absolute;left:10px;top:9px;width:92px;height:92px;border-radius:50%;background:var(--white);display:flex;align-items:center;justify-content:center}
  .band-text{position:absolute;left:119px;top:20px;color:var(--white);font-family:"Oswald",sans-serif;font-weight:600;font-size:28px;line-height:1.14;letter-spacing:.6px}

  .photo{position:absolute;top:855px;width:236px;height:160px;border-radius:16px}
  .photo-depot{left:464px;background:linear-gradient(160deg,#6b7a8c 0%,#a9b1b8 45%,#c4b58a 75%,#3d3d3a 100%)}
  .photo-tanker{left:712px;background:linear-gradient(170deg,#3f5b7d 0%,#8ba0b6 45%,#c9cdd2 65%,#4b4f55 100%)}

  .email-tab{position:absolute;left:285px;top:1049px;width:409px;height:48px;background:var(--red);border-radius:26px 26px 0 0;
    display:flex;align-items:center;justify-content:center;gap:10px;color:var(--white);font-weight:600;font-size:18px}

  .contact-bar{position:absolute;left:39px;top:1096px;width:902px;height:104px;background:var(--bar);border-radius:22px 22px 0 0;display:flex;padding:20px 8px 0 22px}
  .contact{flex:1 1 0;min-width:0;padding:0 10px;border-right:1px solid #3a3a3a;color:var(--white)}
  .contact:last-child{border-right:none}
  .contact-head{display:flex;gap:8px;align-items:flex-start}
  .contact-head svg{flex:none;margin-top:2px}
  .contact-name{color:var(--red);font-weight:600;font-size:16px;line-height:1.1}
  .contact-phone{font-weight:600;font-size:17px;line-height:1.3;white-space:nowrap}
  .contact-mail{font-size:10px;margin-top:6px;color:#eaeaea;white-space:nowrap}
</style>
</head>
<body>
<main class="flyer">

  <div class="hero-photo" role="img" aria-label="Photo of a white road-train fuel tanker parked in front of a large steel depot shed under a blue sky"></div>

  <svg class="hero-shapes" width="980" height="560" viewBox="0 0 980 560" aria-hidden="true">
    <path d="M0 0 H483 C440 170 330 285 160 290 C95 292 40 280 0 262 Z" fill="#666666"/>
    <path d="M0 0 H445 C405 165 300 272 150 274 C90 275 40 265 0 252 Z" fill="#ffffff"/>
    <path d="M0 500 C220 470 420 490 560 535 L0 535 Z" fill="#ffffff"/>
    <path d="M0 512 C210 488 380 498 560 540 L560 548 C380 510 210 500 0 522 Z" fill="#e8302a"/>
  </svg>

  <div class="brand-name">Terra Diesel</div>

  <h1 class="headline"><span class="first">Terra</span> <span class="second">Diesel</span></h1>

  <div class="promise">
    <span><svg class="tick" viewBox="0 0 16 16"><circle cx="8" cy="8" r="8" fill="#e8302a"/><path d="M4.3 8.3l2.4 2.3 5-5" stroke="#fff" stroke-width="2" fill="none"/></svg>RELIABLE</span>
    <span><svg class="tick" viewBox="0 0 16 16"><circle cx="8" cy="8" r="8" fill="#e8302a"/><path d="M4.3 8.3l2.4 2.3 5-5" stroke="#fff" stroke-width="2" fill="none"/></svg>LOCAL</span>
    <span><svg class="tick" viewBox="0 0 16 16"><circle cx="8" cy="8" r="8" fill="#e8302a"/><path d="M4.3 8.3l2.4 2.3 5-5" stroke="#fff" stroke-width="2" fill="none"/></svg>READY TO DELIVER</span>
  </div>

  <svg class="hero-shapes" width="980" height="830" viewBox="0 0 980 830" aria-hidden="true">
    <path d="M560 535 C720 585 860 650 980 700 L980 720 L560 720 Z" fill="#ffffff"/>
    <path d="M560 540 C720 590 870 640 980 690 L980 705 C860 660 720 600 560 548 Z" fill="#e8302a"/>
    <path d="M700 600 C800 610 900 650 980 700 L980 730 L700 730 Z" fill="#e8302a"/>
    <path d="M650 560 C780 575 900 640 980 690 L980 700 C890 650 780 590 650 570 Z" fill="#ffffff"/>
  </svg>

  <section class="services-panel">
    <div class="service" style="top:68px">
      <div class="service-icon">
        <svg width="70" height="54" viewBox="0 0 66 50" fill="none" stroke-width="2.2" stroke-linejoin="round">
          <rect x="4" y="4" width="36" height="26" rx="6" stroke="#e8302a"/>
          <path d="M22 12l5 5-5 5-5-5z" stroke="#e8302a"/>
          <path d="M40 16h12l8 10v10H40z" stroke="#555"/>
          <path d="M2 36h58" stroke="#555"/>
          <circle cx="12" cy="42" r="4.5" stroke="#555"/><circle cx="24" cy="42" r="4.5" stroke="#555"/><circle cx="52" cy="42" r="4.5" stroke="#555"/>
        </svg>
      </div>
      <p class="service-text">Bulk Fuel<br>deliveries</p>
    </div>
    <div class="divider" style="top:196px"></div>

    <div class="service" style="top:215px">
      <div class="service-icon">
        <svg width="66" height="62" viewBox="0 0 64 60" fill="none" stroke-width="2.2" stroke-linejoin="round">
          <path d="M14 34l14-18 10 8-14 18z" stroke="#555"/>
          <path d="M28 16l8-8 16-4 2 4-14 6 4 6" stroke="#555"/>
          <path d="M14 34l-8 20" stroke="#555"/>
          <path d="M52 20c0 0-6 8-6 12a6 6 0 0 0 12 0c0-4-6-12-6-12z" stroke="#e8302a"/>
        </svg>
      </div>
      <p class="service-text">Oils &amp;<br>lubricants</p>
    </div>
    <div class="divider" style="top:344px"></div>

    <div class="service" style="top:373px">
      <div class="service-icon" role="img" aria-label="Family owned small business badge">
        <svg width="86" height="86" viewBox="0 0 80 80"><circle cx="40" cy="40" r="34" fill="none" stroke="#555" stroke-width="2.2"/><circle cx="40" cy="40" r="16" fill="#e8302a" opacity=".85"/></svg>
      </div>
      <p class="service-text">Local<br>Family owned<br>business</p>
    </div>
  </section>

  <div class="base-badge">
    <div role="img" aria-label="Map of south-western New South Wales" style="position:absolute;inset:0;background:radial-gradient(circle at 40% 60%,#e9e9e9,#dadada)"></div>
    <div class="base-text">
      <div class="small">BASED IN</div>
      <div class="town">GRIFFITH</div>
      <div class="state">NSW</div>
    </div>
    <svg class="pin" width="30" height="42" viewBox="0 0 28 40"><path d="M14 0a14 14 0 0 1 14 14c0 10-14 26-14 26S0 24 0 14A14 14 0 0 1 14 0z" fill="#e8302a"/><circle cx="14" cy="14" r="5.5" fill="#fff"/></svg>
  </div>

  <div class="service-band">
    <div class="band-icon">
      <svg width="68" height="40" viewBox="0 0 60 36" fill="none" stroke="#222" stroke-width="2.2" stroke-linejoin="round">
        <rect x="16" y="2" width="42" height="24"/>
        <path d="M16 10H7l-5 8v8h14"/>
        <path d="M2 26h56"/>
        <circle cx="10" cy="30" r="4"/><circle cx="40" cy="30" r="4"/><circle cx="50" cy="30" r="4"/>
      </svg>
    </div>
    <p class="band-text">SERVICING GRIFFITH<br>AREA &amp; SURROUNDS</p>
  </div>

  <div class="photo photo-depot" role="img" aria-label="Photo of fuel storage tanks and refinery stack at dusk"></div>
  <div class="photo photo-tanker" role="img" aria-label="Photo of a silver fuel tanker truck driving on a highway"></div>

  <div class="email-tab">
    <svg width="24" height="17" viewBox="0 0 22 16" fill="none" stroke="#fff" stroke-width="1.6"><rect x="1" y="1" width="20" height="14"/><path d="M1 1l10 8 10-8M1 15l7-7M21 15l-7-7"/></svg>
    Fuel@terradiesel-example.com.au
  </div>

  <footer class="contact-bar">
    <div class="contact">
      <div class="contact-head">
        <svg width="32" height="32" viewBox="0 0 30 30" fill="none" stroke="#fff" stroke-width="1.8"><path d="M6 3l5 6-3 3c2 4 5 7 9 9l3-3 6 5-3 4C12 26 4 18 2 7z"/><path d="M17 4a9 9 0 0 1 9 9M17 9a4 4 0 0 1 4 4"/></svg>
        <div><div class="contact-name">Owen</div><div class="contact-phone">0491 570 362</div></div>
      </div>
      <div class="contact-mail">ohartley@terradiesel-example.com.au</div>
    </div>
    <div class="contact">
      <div class="contact-head">
        <svg width="32" height="32" viewBox="0 0 30 30" fill="none" stroke="#fff" stroke-width="1.8"><path d="M6 3l5 6-3 3c2 4 5 7 9 9l3-3 6 5-3 4C12 26 4 18 2 7z"/><path d="M17 4a9 9 0 0 1 9 9M17 9a4 4 0 0 1 4 4"/></svg>
        <div><div class="contact-name">Liam</div><div class="contact-phone">0491 570 718</div></div>
      </div>
      <div class="contact-mail">lprosser@terradiesel-example.com.au</div>
    </div>
    <div class="contact">
      <div class="contact-head">
        <svg width="32" height="32" viewBox="0 0 30 30" fill="none" stroke="#fff" stroke-width="1.8"><path d="M6 3l5 6-3 3c2 4 5 7 9 9l3-3 6 5-3 4C12 26 4 18 2 7z"/><path d="M17 4a9 9 0 0 1 9 9M17 9a4 4 0 0 1 4 4"/></svg>
        <div><div class="contact-name">Simon</div><div class="contact-phone">0491 570 905</div></div>
      </div>
      <div class="contact-mail">skenway@terradiesel-example.com.au</div>
    </div>
    <div class="contact">
      <div class="contact-head">
        <svg width="32" height="32" viewBox="0 0 30 30" fill="none" stroke="#fff" stroke-width="1.8"><path d="M6 3l5 6-3 3c2 4 5 7 9 9l3-3 6 5-3 4C12 26 4 18 2 7z"/><path d="M17 4a9 9 0 0 1 9 9M17 9a4 4 0 0 1 4 4"/></svg>
        <div><div class="contact-name">Office</div><div class="contact-phone">02 5550 1734</div></div>
      </div>
    </div>
  </footer>

</main>
</body>
</html>
```